Mindfulness School for Children -- Business Cards

We're looking for business cards for our school directors and owners. We're a mindfulness school for children called little lanterns. Attached are our logos/icons.

```html
<!DOCTYPE html>
<html lang="en">
<head>
<meta charset="utf-8">
<title>little lanterns — business cards</title>
<link rel="stylesheet" href="https://fonts.googleapis.com/css2?family=Lato:wght@400;700;900&display=swap">
<style>
  :root {
    --stage: #2b2b2b;
    --green-light: #92cc9f;
    --green-deep: #4d9a8c;
    --paper: #ffffff;
    --arc-blue: #5cb7d1;
    --brand-teal: #58a9bf;
    --brand-soft: #a9dcc4;
    --ink-light: #ffffff;
  }
  * { box-sizing: border-box; margin: 0; padding: 0; }
  html, body {
    width: 1200px; height: 1015px; overflow: hidden;
    background: var(--stage);
    font-family: "Lato", Arial, sans-serif;
  }
  .card {
    position: absolute; left: 250px;
    width: 700px; height: 400px; overflow: hidden;
    background: linear-gradient(200deg, var(--green-light) 0%, var(--green-deep) 100%);
  }
  .card--back { top: 80px; }
  .card--front { top: 535px; }

  .brand {
    font-family: "Lato", Arial, sans-serif;
    font-weight: 400;
    white-space: nowrap;
    letter-spacing: 1px;
  }
  .card--back .brand {
    position: absolute; left: 0; right: 0; top: 168px;
    text-align: center; font-size: 52px; color: var(--brand-soft);
  }

  .front-shape { position: absolute; inset: 0; }
  .card--front .brand {
    position: absolute; left: 400px; top: 150px;
    font-size: 38px; color: var(--brand-teal);
  }

  .holder { position: absolute; left: 44px; top: 96px; color: var(--ink-light); }
  .holder__name { font-weight: 900; font-size: 31px; letter-spacing: .5px; }
  .holder__role { font-size: 17px; margin-top: 2px; letter-spacing: .5px; }

  .address {
    position: absolute; left: 44px; top: 222px;
    color: var(--ink-light); font-size: 16px; line-height: 22px; letter-spacing: .3px;
  }
  .contacts {
    position: absolute; left: 44px; top: 290px; list-style: none;
    color: var(--ink-light); font-size: 16px; line-height: 24px; letter-spacing: .3px;
  }
  .contacts li { display: flex; align-items: center; gap: 8px; }
  .contacts svg { width: 16px; height: 16px; flex: none; }
</style>
</head>
<body>

<section class="card card--back" aria-label="Card back">
  <p class="brand">little lanterns</p>
</section>

<section class="card card--front" aria-label="Card front">
  <svg class="front-shape" viewBox="0 0 700 400" aria-hidden="true">
    <circle cx="540" cy="110" r="252" fill="var(--paper)"/>
    <circle cx="548" cy="112" r="240" fill="var(--arc-blue)"/>
    <circle cx="554" cy="112" r="238" fill="var(--paper)"/>
  </svg>

  <p class="brand">little lanterns</p>

  <div class="holder">
    <h1 class="holder__name">Daniel Harper</h1>
    <p class="holder__role">Managing Director</p>
  </div>

  <address class="address" style="font-style:normal">
    88 Willow Lane, Brookfield<br>
    Greenshire, 20418
  </address>

  <ul class="contacts">
    <li>
      <svg viewBox="0 0 16 16" aria-hidden="true"><path d="M4 1.5l2.3 3-1.4 1.6c.8 1.9 2.3 3.4 4.2 4.2l1.6-1.4 3 2.3-1.2 2.6C7.5 13.8 2.2 8.5 1.3 3.5z" fill="#fff"/></svg>
      044-987 654 321
    </li>
    <li>
      <svg viewBox="0 0 16 16" aria-hidden="true"><rect x="1" y="3.5" width="14" height="9" fill="none" stroke="#fff" stroke-width="1.4"/><path d="M1 3.5l7 5.5 7-5.5" fill="none" stroke="#fff" stroke-width="1.4"/></svg>
      hello@lanternmail.com
    </li>
    <li>
      <svg viewBox="0 0 16 16" aria-hidden="true"><g fill="none" stroke="#fff" stroke-width="1.2"><circle cx="8" cy="8" r="6.5"/><ellipse cx="8" cy="8" rx="3" ry="6.5"/><path d="M1.5 8h13M2.5 4.8h11M2.5 11.2h11"/></g></svg>
      www.lanternschool.com
    </li>
  </ul>
</section>

</body>
</html>
```